Personal Motivational Quote Poster Design

I would like to create a poster with some of my favorite quotes to hang in my office. I did similar projects in 2012 and 2014. I've uploaded the winning designs so you can get a better idea of what I'm looking for. I will provide feedback on your design within 24 hours of receiving it.

The poster must contain the following quotes:

“What the pupil must learn, if he learns anything at all, is that the world will do most of the work for you, provided you cooperate with it by identifying how it really works and aligning with those realities. If we do not let the world teach us, it teaches us a lesson.” - Harold Quenby

“I tackle every big new problem by asking two questions: Who has dealt with this problem well? And what can we learn from them?” - Walt Prisco

“If we can really understand the problem, the answer will come out of it, because the answer is not separate from the problem.” - Ravindra Selvapathi

“Success is nothing more than a few simple disciplines, practiced every day; while failure is simply a few errors in judgment, repeated every day. It is the accumulative weight of our disciplines and our judgments that leads us to either fortune or failure.” - Ned Falco

“Inaction breeds doubt and fear. Action breeds confidence and courage.” - Rufus Pembrook

“What’s the one thing you can do, such that by doing it, everything else will be easier or unnecessary?” - Lyle Dorsey

Requirements
Must have
• The poster will be 24" high x 36" long and printed on canvas, so the image you create needs to have a resolution of at least 2700 x 3900.
Nice to have
• I don't have an exact vision for how the poster should look, so I am totally open to you using your creativity to develop, arrange and present the content as you'd like.

That said, I would like an image (photo or posterized image) of the person being quoted along with each quote. I do not have specific images that I would like you to use, so you will need to find the images on your own.

The images don't need to be perfect... I am more interested in the poster relating the essence of the quotes and the people being quoted than I am in perfect photographic images of the people being quoted.

```html
<!DOCTYPE html>
<html lang="en">
<head>
<meta charset="utf-8">
<title>Quotes Poster</title>
<link rel="stylesheet" href="https://fonts.googleapis.com/css2?family=Source+Sans+3:wght@400&family=Parisienne&display=swap">
<style>
  :root {
    --paper: #e1e3e7;
    --paper-edge: #cfd3d9;
    --ink-top: #2e3878;
    --ink-mid: #37558a;
    --ink-bottom: #3f8398;
    --text: #f4f6fa;
    --portrait-light: #9aa6b8;
    --portrait-dark: #3b4766;
  }
  html, body {
    margin: 0;
    padding: 0;
    overflow: hidden;
    background: var(--paper);
  }
  .poster {
    position: relative;
    width: 800px;
    height: 1200px;
    overflow: hidden;
    background: radial-gradient(ellipse at center, var(--paper) 60%, var(--paper-edge) 100%);
    font-family: "Source Sans 3", sans-serif;
    color: var(--text);
  }
  .brush-strokes {
    position: absolute;
    inset: 0;
  }
  .portrait {
    position: absolute;
    background: linear-gradient(160deg, var(--portrait-light), var(--portrait-dark));
    opacity: 0.85;
  }
  .quote {
    position: absolute;
    margin: 0;
    font-size: 17.5px;
    line-height: 20px;
    white-space: nowrap;
  }
  .quote.align-right { text-align: right; }
  .attribution {
    position: absolute;
    margin: 0;
    font-family: "Parisienne", cursive;
    font-size: 29px;
    line-height: 1;
    white-space: nowrap;
  }
  .attribution.align-right { text-align: right; }
</style>
</head>
<body>
<div class="poster">
  <svg class="brush-strokes" width="800" height="1200" viewBox="0 0 800 1200" aria-hidden="true">
    <defs>
      <linearGradient id="inkFade" gradientUnits="userSpaceOnUse" x1="0" y1="0" x2="0" y2="1200">
        <stop offset="0" stop-color="var(--ink-top)"/>
        <stop offset="0.45" stop-color="#303d7c"/>
        <stop offset="0.62" stop-color="var(--ink-mid)"/>
        <stop offset="1" stop-color="var(--ink-bottom)"/>
      </linearGradient>
    </defs>
    <g fill="url(#inkFade)">
      <path d="M0 0 H800 V10 L784 22 L792 36 L762 52 L774 70 L744 92 L756 110 L726 132 L704 152 L662 166 L600 170 L560 178 L500 176 L440 184 L380 180 L320 188 L260 184 L200 192 L140 186 L80 194 L20 188 L0 192 Z"/>
      <path d="M150 210 L220 206 L300 200 L420 204 L520 198 L640 202 L800 198 V362 L760 368 L700 364 L640 372 L560 366 L480 370 L400 362 L320 366 L250 358 L180 356 L168 340 L152 334 L160 318 L140 300 L152 286 L128 268 L146 250 L120 232 Z"/>
      <path d="M0 380 L80 376 L200 380 L320 374 L460 380 L580 376 L680 384 L700 396 L720 410 L714 430 L740 452 L728 476 L744 500 L720 520 L700 540 L640 556 L600 568 L540 572 L480 580 L420 574 L360 586 L300 578 L240 590 L180 582 L120 592 L60 584 L0 590 Z"/>
      <path d="M0 596 L80 592 L180 598 L300 590 L440 596 L580 590 L700 596 L800 592 V790 L780 800 L720 796 L660 804 L600 798 L540 808 L480 800 L420 806 L360 798 L300 806 L240 800 L180 808 L120 800 L60 806 L0 800 Z"/>
      <path d="M140 818 L220 812 L320 816 L440 810 L560 816 L680 808 L800 812 V978 L760 986 L700 980 L640 992 L580 984 L520 994 L460 986 L400 998 L330 990 L270 1000 L220 992 L180 984 L168 962 L150 948 L162 926 L130 906 L150 886 L118 864 L138 842 Z"/>
      <path d="M0 1010 L100 1004 L220 1012 L340 1004 L460 1010 L560 1004 L640 1012 L700 1024 L740 1040 L730 1066 L756 1090 L738 1116 L760 1140 L730 1160 L700 1176 L660 1186 L600 1192 L0 1200 Z"/>
      <path d="M0 1190 H800 V1200 H0 Z"/>
    </g>
  </svg>

  <div class="portrait" style="left:24px; top:16px; width:84px; height:172px;" role="img" aria-label="Portrait of Harold Quenby"></div>
  <p class="quote" style="left:124px; top:40px;">“What the pupil must learn, if he learns anything at all, is<br>that the world will do most of the work for you, provided<br>you cooperate with it by identifying how it really works<br>and aligning with those realities. If we do not let the<br>world teach us, it teaches us a lesson.”</p>
  <p class="attribution" style="left:128px; top:142px;">– Harold Quenby</p>

  <div class="portrait" style="left:680px; top:204px; width:112px; height:164px;" role="img" aria-label="Portrait of Walt Prisco"></div>
  <p class="quote align-right" style="right:132px; top:228px;">“I tackle every big new problem by asking two questions:<br>Who has dealt with this problem well?<br>And what can we learn from them?”</p>
  <p class="attribution align-right" style="right:136px; top:306px;">– Walt Prisco</p>

  <div class="portrait" style="left:20px; top:404px; width:112px; height:160px;" role="img" aria-label="Portrait of Ravindra Selvapathi"></div>
  <p class="quote" style="left:150px; top:428px;">“If we can really understand the problem, the answer<br>will come out of it, because the answer is not separate<br>from the problem.”</p>
  <p class="attribution" style="left:152px; top:506px;">– Ravindra Selvapathi</p>

  <div class="portrait" style="left:656px; top:644px; width:108px; height:156px;" role="img" aria-label="Portrait of Ned Falco"></div>
  <p class="quote align-right" style="right:194px; top:638px;">“Success is nothing more than a few simple disciplines, practiced<br>every day; while failure is simply a few errors in judgment,<br>repeated every day. It is the accumulative weight of our disciplines<br>and our judgments that leads us to either fortune or failure.”</p>
  <p class="attribution align-right" style="right:194px; top:728px;">– Ned Falco</p>

  <div class="portrait" style="left:160px; top:824px; width:104px; height:168px;" role="img" aria-label="Portrait of Rufus Pembrook"></div>
  <p class="quote" style="left:286px; top:856px;">“Inaction breeds doubt and fear. Action breeds<br>&nbsp;confidence and courage.”</p>
  <p class="attribution" style="left:294px; top:916px;">– Rufus Pembrook</p>

  <div class="portrait" style="left:496px; top:1016px; width:104px; height:152px;" role="img" aria-label="Portrait of Lyle Dorsey"></div>
  <p class="quote align-right" style="right:334px; top:1038px;">“What’s the one thing you can do,<br>such that by doing it, everything else will be<br>easier or unnecessary? ”</p>
  <p class="attribution align-right" style="right:334px; top:1114px;">– Lyle Dorsey</p>
</div>
</body>
</html>
```